The design should look similar to the uploaded example to accommodate the information needed for a business card template. I would like to see the colors orange and charcoal grey incorporated along with the logo.The following should be on the back of the card SPECIALIZING IN NEW AND USED TIRES & WHEELS FOR:- Loaders- Skid Steers- Telehandlers- Boom Lifts- Forklifs and moreELIMINATING DOWNTIMEWheel Exchange Program for New & Used Foam Filled and Solid Rubber TiresSPECIALTY SERVICES- Foam Filling Tires- Largest Tire Press in SE- ONSITE Forklift Tire Press- Boom Truck Services - Rubber Tracks

Target Market(s)

New and Existing Customers

Industry/Entity Type

Business

Contact Information for Business Card

NAMEHEAVY DUTY TIRE, LLC8470 Belvedere RoadWest Palm Beach, FL 33411P: 844-HD-TIRESF: 561-431-6469C:E: W: WWW.GRANITERIMSUPPLY-EXAMPLE.COM

Font styles to use
Sans Serif

Colors
f37122
333333

Requirements
Must have
• The logo and the information indicated for the backside of the card
Nice to have
• Keep the orange and charcoal grey colors

```html
<!DOCTYPE html>
<html lang="en">
<head>
<meta charset="utf-8">
<title>Granite Rim Supply, LLC — Business Card</title>
<link rel="stylesheet" href="https://fonts.googleapis.com/css2?family=Open+Sans:wght@400;600;700;800&display=swap">
<style>
  :root {
    --orange: #f37122;
    --charcoal: #333333;
    --slate: #3c4752;
    --slate-dark: #323b45;
    --paper: #ffffff;
    --mist: #d9dde1;
    --stage: #eceae6;
    --text-light: #e6e9ec;
  }
  * { box-sizing: border-box; margin: 0; padding: 0; }
  html, body { width: 1200px; height: 950px; overflow: hidden; }
  body {
    background: var(--stage);
    font-family: "Open Sans", Arial, sans-serif;
    position: relative;
  }
  .card {
    position: absolute;
    left: 250px;
    width: 700px;
    height: 400px;
    border-radius: 6px;
    overflow: hidden;
    box-shadow: 0 6px 18px rgba(0,0,0,0.18);
  }

  /* ---------- Back side ---------- */
  .card-back {
    top: 45px;
    background: linear-gradient(160deg, var(--slate) 0%, var(--slate-dark) 100%);
    color: var(--text-light);
    padding: 34px 40px;
    text-align: center;
  }
  .brand {
    display: flex;
    align-items: center;
    gap: 14px;
  }
  .brand-dot {
    width: 44px; height: 44px;
    border-radius: 50%;
    background: var(--orange);
    flex: none;
  }
  .brand-name {
    font-weight: 800;
    font-size: 26px;
    letter-spacing: 0.5px;
    line-height: 1.05;
    text-align: left;
  }
  .card-back .brand { justify-content: center; margin-bottom: 26px; }
  .card-back .brand-name { color: var(--paper); }
  .service-block { margin-bottom: 16px; }
  .service-heading {
    font-weight: 800;
    font-size: 17px;
    letter-spacing: 0.4px;
    color: var(--paper);
    text-transform: uppercase;
  }
  .service-line {
    font-size: 14.5px;
    line-height: 1.45;
  }
  .bullet { color: var(--orange); margin: 0 6px; }

  /* ---------- Front side ---------- */
  .card-front {
    top: 505px;
    background: var(--slate);
  }
  .front-shape { position: absolute; inset: 0; }
  .front-content {
    position: absolute;
    inset: 0;
    padding: 34px 36px;
    color: var(--charcoal);
  }
  .card-front .brand-name { color: var(--charcoal); font-size: 25px; }
  .contact {
    margin-top: 30px;
    font-size: 17px;
    line-height: 1.38;
    list-style: none;
  }
  .contact-address { margin-bottom: 2px; }
  .contact-item { display: flex; align-items: center; gap: 9px; }
  .contact-item svg { width: 15px; height: 15px; fill: var(--charcoal); flex: none; }
  .person {
    position: absolute;
    right: 108px;
    top: 188px;
    text-align: right;
  }
  .person-name {
    font-size: 20px;
    font-weight: 600;
    letter-spacing: 0.5px;
    color: var(--slate);
  }
  .person-title {
    font-size: 17px;
    font-weight: 600;
    letter-spacing: 0.8px;
    color: var(--orange);
  }
</style>
</head>
<body>

  <section class="card card-back" aria-label="Card back">
    <div class="brand">
      <span class="brand-dot"></span>
      <span class="brand-name">GRANITE RIM<br>SUPPLY, LLC</span>
    </div>

    <div class="service-block">
      <p class="service-heading">Specializing in New and Used Tires &amp; Wheels for</p>
      <p class="service-line">Loaders<span class="bullet">•</span>Skid Steers<span class="bullet">•</span>Telehandlers<span class="bullet">•</span>Boom Lifts<span class="bullet">•</span>Forklifts and more</p>
    </div>

    <div class="service-block">
      <p class="service-heading">Eliminating Downtime</p>
      <p class="service-line">Wheel Exchange Program for New &amp; Used Foam Filled and Solid Rubber Tires</p>
    </div>

    <div class="service-block">
      <p class="service-heading">Specialty Services</p>
      <p class="service-line">Foam Filling Tires<span class="bullet">•</span>Largest Tire Press in SE<span class="bullet">•</span>ONSITE Forklift Tire Press</p>
      <p class="service-line">Boom Truck Services<span class="bullet">•</span>Rubber Tracks</p>
    </div>
  </section>

  <section class="card card-front" aria-label="Card front">
    <svg class="front-shape" viewBox="0 0 700 400" preserveAspectRatio="none" aria-hidden="true">
      <path d="M200,400 C420,392 600,330 655,215 C640,320 540,385 360,400 Z" fill="#c9ced3"/>
      <path d="M220,400 C410,392 570,335 640,225 C630,310 520,382 330,400 Z" fill="var(--orange)"/>
      <path d="M0,0 H560 C690,60 700,230 575,315 C480,375 370,400 240,400 H0 Z" fill="var(--paper)"/>
    </svg>

    <div class="front-content">
      <div class="brand">
        <span class="brand-dot"></span>
        <span class="brand-name">GRANITE RIM<br>SUPPLY, LLC</span>
      </div>

      <ul class="contact">
        <li class="contact-address">5126 Marston Lane<br>Lake Corbin, FL 33470</li>
        <li class="contact-item">
          <svg viewBox="0 0 16 16"><path d="M3 1.5h3l1.2 3-1.8 1.2a8 8 0 0 0 4 4l1.2-1.8 3 1.2v3c0 .8-.7 1.4-1.5 1.4A12.5 12.5 0 0 1 1.6 3C1.6 2.2 2.2 1.5 3 1.5z"/></svg>
          844-GR-WHEEL
        </li>
        <li class="contact-item">
          <svg viewBox="0 0 16 16"><path d="M4.5 0.5h7a1 1 0 0 1 1 1v13a1 1 0 0 1-1 1h-7a1 1 0 0 1-1-1v-13a1 1 0 0 1 1-1zm.8 2v9.5h5.4V2.5zM8 12.8a.9.9 0 1 0 0 1.8.9.9 0 0 0 0-1.8z"/></svg>
          836 417 2290
        </li>
        <li class="contact-item">
          <svg viewBox="0 0 16 16"><path d="M4 1h6l2 2v3H4zM1 7h14v6h-2v2H3v-2H1zm4 4v3h6v-3z"/></svg>
          561-278-9053
        </li>
        <li class="contact-item">
          <svg viewBox="0 0 16 16"><path d="M1 3h14v10H1zm1.5 1.3v.4L8 8.8l5.5-4.1v-.4z"/></svg>
          hello@graniterim-example.com
        </li>
        <li class="contact-item">
          <svg viewBox="0 0 16 16"><circle cx="8" cy="8" r="7"/><path d="M1.5 8h13M8 1c-2.5 2.5-2.5 11.5 0 14M8 1c2.5 2.5 2.5 11.5 0 14" stroke="#fff" stroke-width="1" fill="none"/></svg>
          www.graniterimsupply-example.com
        </li>
      </ul>

      <div class="person">
        <p class="person-name">DANA WHITFIELD</p>
        <p class="person-title">PRESIDENT</p>
      </div>
    </div>
  </section>

</body>
</html>
```